Advanced Therapeutic Massage Therapist

I need a business card advertising my massage services as an advanced therapeutic massage therapist. I offer advanced therapeutic massage, swedish and deep tissue. I want to create a simple, professional and feminine card. I like bright colours and creativity.

I prefer a bold and experimental approach rather than something status-quo. A card to suggest therapeutic healing through dynamic massage. Motifs, shapes or layout which suggest movement and flow.
Updates

Target Market(s)

Everybody!

Industry/Entity Type

Health And Wellness

Contact Information for Business Card

The card should include:
My name, logo, services offered and my contact details.

Sláine Dunleavy
Massage Therapist

- Swedish - Deep Tissue - Advanced Therapeutic

Phone: (+353) 87 216 4093
Email: regenerate@slainedunleavy-example.com
Website: www.slainedunlevy-example.com

Font styles to use
Serif
Sans Serif
Decorative
Script

Colors

Designer to choose colors to be used in the design.

Requirements
Must have
• An example may contain something like this, yet concise:
• "Sláine Dunleavy
• Massage Therapist
• - Swedish - Deep Tissue - Advanced Therapeutic"
Nice to have
• This sentence is optional:
• Imagery such as a logo or symbol. I have attached a file containing a logo I had produced however the name is incorrect now as it is "Sláine" not "Nelly". It could be edited to change it to Sláine.
• I have sent the file as .psd .jpg. .pdf and .png
• I like when the card conveys energy, movement, pressure points, flow etc.
• I just like the designer to follow their own style and ideas. I like bright colours but must have a lot of a base colour to offset it. I really prefer them to follow their own inspiration. That is my preference.
Should not have
• Pine trees, non-native trees to Britain and Ireland, exotic flowers or animals that are not native to Britain and Ireland.
• I don't like brown as the background colour of the card.
• The cars shouldn't look like a wedding invitation i.e too many floral type designs.

```html
<!DOCTYPE html>
<html lang="en">
<head>
<meta charset="utf-8">
<title>Sláine Dunleavy – Massage Therapist Business Card</title>
<link rel="stylesheet" href="https://fonts.googleapis.com/css2?family=Work+Sans:wght@400;500;700&display=swap">
<style>
  :root {
    --charcoal: #3b3b3b;
    --gold: #c9952f;
    --mint: #a9ddd0;
    --white: #ffffff;
    --soft-white: #e9e9e9;
    --backdrop: #d9d9d9;
  }
  * { box-sizing: border-box; margin: 0; padding: 0; }
  html, body {
    width: 1200px; height: 900px; overflow: hidden;
    background: var(--backdrop);
    font-family: "Work Sans", Arial, sans-serif;
  }
  .card {
    position: absolute; left: 260px;
    width: 680px; height: 410px;
    border-radius: 22px; overflow: hidden;
    box-shadow: 0 10px 28px rgba(0,0,0,.25);
  }
  /* Back of card */
  .card-back { top: 30px; background: var(--charcoal); color: var(--white); }
  .brand {
    position: absolute; top: 78px; left: 0; right: 0;
    display: flex; flex-direction: column; align-items: center;
  }
  .brand-mark { width: 150px; height: 150px; border-radius: 50%; background: var(--mint); }
  .brand-name { margin-top: 18px; font-size: 26px; font-weight: 400; letter-spacing: .5px; }
  .brand-role { margin-top: 2px; font-size: 13px; letter-spacing: 2px; color: var(--soft-white); }
  .tagline {
    position: absolute; left: 0; right: 0; bottom: 44px;
    text-align: center; font-size: 16px; color: var(--soft-white);
  }
  /* Front of card */
  .card-front { top: 460px; background: var(--white); }
  .wave { position: absolute; inset: 0; }
  .front-mark {
    position: absolute; left: 70px; top: 22px;
    display: flex; align-items: center; gap: 16px;
  }
  .front-mark .circle { width: 110px; height: 110px; border-radius: 50%; background: var(--gold); }
  .front-mark .mark-name { font-size: 22px; font-weight: 500; color: var(--gold); }
  .details {
    position: absolute; right: 46px; bottom: 22px;
    text-align: right; color: var(--white);
  }
  .details .name {
    font-size: 26px; font-weight: 700; color: var(--gold);
    text-transform: uppercase; letter-spacing: .5px; line-height: 1.1;
  }
  .details .role { font-size: 13px; letter-spacing: 1.5px; text-transform: uppercase; margin-bottom: 5px; }
  .details .line {
    font-size: 15px; line-height: 1.3;
    display: flex; justify-content: flex-end; align-items: center; gap: 10px;
  }
  .icon { width: 14px; height: 14px; flex: none; }
  .services { margin-top: 4px; }
</style>
</head>
<body>

<section class="card card-back" aria-label="Back of business card">
  <div class="brand">
    <div class="brand-mark"></div>
    <div class="brand-name">Sláine Dunleavy</div>
    <div class="brand-role">massage therapist</div>
  </div>
  <p class="tagline">VTQB qualified specialising in advanced therapeutic and deep tissue massage.</p>
</section>

<section class="card card-front" aria-label="Front of business card">
  <svg class="wave" viewBox="0 0 680 410" preserveAspectRatio="none" aria-hidden="true">
    <path d="M0,115 C20,175 80,190 200,185 C330,179 430,162 520,162 C600,162 650,180 680,202 L680,190 C650,166 600,148 520,148 C430,148 330,164 200,170 C90,175 24,160 0,95 Z" fill="var(--gold)"/>
    <path d="M0,150 C30,200 90,210 200,203 C330,195 430,178 520,178 C600,178 650,195 680,220 L680,410 L0,410 Z" fill="var(--charcoal)"/>
    <path d="M520,172 C600,172 655,198 680,240 L680,270 C660,225 610,190 520,172 Z" fill="var(--gold)"/>
  </svg>

  <div class="front-mark">
    <div class="circle"></div>
    <div class="mark-name">Sláine Dunleavy</div>
  </div>

  <div class="details">
    <div class="name">Sláine Dunleavy</div>
    <div class="role">Massage Therapist</div>
    <div class="line">(+353) 87 216 4093
      <svg class="icon" viewBox="0 0 16 16" aria-hidden="true"><path d="M4 1l3 3-2 2c1 2 3 4 5 5l2-2 3 3-2 3C7 15 1 9 1 3z" fill="var(--gold)"/></svg>
    </div>
    <div class="line">regenerate@slainedunleavy-example.com
      <svg class="icon" viewBox="0 0 16 16" aria-hidden="true"><rect x="1.5" y="3.5" width="13" height="9" fill="none" stroke="var(--gold)" stroke-width="1.6"/><path d="M2 4l6 5 6-5" fill="none" stroke="var(--gold)" stroke-width="1.6"/></svg>
    </div>
    <div class="line">www.slainedunlevy-example.com
      <svg class="icon" viewBox="0 0 16 16" aria-hidden="true"><circle cx="8" cy="8" r="6.2" fill="none" stroke="var(--gold)" stroke-width="1.6"/><path d="M2 8h12M8 2c-3 3-3 9 0 12M8 2c3 3 3 9 0 12" fill="none" stroke="var(--gold)" stroke-width="1.2"/></svg>
    </div>
    <div class="services">
      <div class="line">Swedish
        <svg class="icon" viewBox="0 0 16 16" aria-hidden="true"><path d="M11 3L5 8l6 5" fill="none" stroke="var(--gold)" stroke-width="2"/></svg>
      </div>
      <div class="line">Deep Tissue
        <svg class="icon" viewBox="0 0 16 16" aria-hidden="true"><path d="M11 3L5 8l6 5" fill="none" stroke="var(--gold)" stroke-width="2"/></svg>
      </div>
      <div class="line">Advanced Therapeutic
        <svg class="icon" viewBox="0 0 16 16" aria-hidden="true"><path d="M11 3L5 8l6 5" fill="none" stroke="var(--gold)" stroke-width="2"/></svg>
      </div>
    </div>
  </div>
</section>

</body>
</html>
```